Calvanto Group Real Estate Company business cards

New business card design, we are generally happy with the basic layout of the existing front of business card, (feel free to change) but require a head shot photo on the back side.

http://www.calvanto.com.au/

Attached logos, and existing business card

------------------------------

Target Market(s)

Real estate

Industry/Entity Type

Real Estate

Contact Information for Business Card

Standard size double sided

Font styles to use
Other font styles liked:
• Futura

Requirements
Must have
• Photo head shot on the back side
Nice to have
• yes
Should not have
• No

```html
<!DOCTYPE html>
<html lang="en">
<head>
<meta charset="utf-8">
<title>Calvanto Group – Business Cards</title>
<link rel="stylesheet" href="https://fonts.googleapis.com/css2?family=Jost:wght@400;500;600&family=Open+Sans:wght@400;600&display=swap">
<style>
  :root {
    --stage: #3a3a3a;
    --paper: #f7f7f7;
    --purple: #2b1a5e;
    --orange: #ef8a1d;
    --ink: #3c3c3c;
    --white: #ffffff;
    --rule: #e2b98a;
    --photo-top: #d98a3a;
    --photo-bottom: #2a3550;
  }
  * { margin: 0; padding: 0; box-sizing: border-box; }
  html, body { width: 1200px; height: 750px; overflow: hidden; }
  body { background: var(--stage); position: relative; font-family: "Open Sans", Arial, sans-serif; }

  .card { position: absolute; top: 228px; width: 462px; height: 263px; overflow: hidden; }
  .card-front { left: 124px; background: var(--paper); }
  .card-back { left: 618px; background: var(--orange); }

  /* Front */
  .brand { position: absolute; left: 236px; top: 50px; width: 208px; text-align: center; white-space: nowrap; }
  .brand-name { font-family: "Jost", sans-serif; font-weight: 500; font-size: 25px; color: var(--purple); line-height: 1; letter-spacing: 0.3px; }
  .services { position: absolute; top: 88px; left: 236px; width: 208px; text-align: center; white-space: nowrap;
    font-family: "Jost", sans-serif; font-weight: 600; font-size: 11.5px; line-height: 14px; color: var(--purple); }
  .services span { margin: 0 6px; }

  .name-marker { position: absolute; left: 0; top: 141px; width: 9px; height: 33px; background: var(--purple); }
  .person-name { position: absolute; left: 23px; top: 138px; font-family: "Jost", sans-serif; font-weight: 500; font-size: 18.5px; line-height: 24px; color: var(--purple); white-space: nowrap; }
  .person-title { position: absolute; left: 23px; top: 160px; font-family: "Jost", sans-serif; font-size: 13px; line-height: 16px; color: var(--orange); }
  .divider { position: absolute; left: 72px; right: 24px; top: 171px; height: 1px; background: var(--rule); }

  .contact { position: absolute; left: 24px; top: 186px; list-style: none; font-size: 11.5px; color: var(--ink); }
  .contact li { display: flex; align-items: center; height: 18px; white-space: nowrap; }
  .contact svg { width: 12px; height: 12px; margin-right: 6px; fill: var(--purple); }

  .company { position: absolute; right: 24px; top: 183px; text-align: right; color: var(--ink); font-size: 11.5px; line-height: 17px; white-space: nowrap; }
  .company strong { font-weight: 600; }

  .band-purple { position: absolute; left: 0; bottom: 0; width: 275px; height: 9px; background: var(--purple); }
  .band-orange { position: absolute; right: 0; bottom: 0; width: 198px; height: 29px; background: var(--orange);
    clip-path: polygon(26px 0, 100% 0, 100% 100%, 0 100%); }
  .band-orange a { position: absolute; right: 19px; top: 6px; color: var(--white); text-decoration: none; font-size: 11.5px; letter-spacing: 1px; white-space: nowrap; }

  /* Back */
  .headshot { position: absolute; left: 38px; top: 16px; width: 178px; height: 247px;
    background: linear-gradient(180deg, var(--photo-top) 0%, var(--photo-bottom) 45%, var(--photo-bottom) 100%);
    border-radius: 80px 80px 0 0; }
  .back-brand { position: absolute; left: 262px; top: 150px; width: 170px; text-align: center; white-space: nowrap;
    font-family: "Jost", sans-serif; font-weight: 500; font-size: 30px; color: var(--white); }
  .back-url { position: absolute; left: 262px; top: 230px; width: 170px; text-align: center; white-space: nowrap;
    color: var(--white); font-size: 11.5px; letter-spacing: 1.2px; text-decoration: none; }
</style>
</head>
<body>
  <section class="card card-front" aria-label="Business card front">
    <div class="brand"><div class="brand-name">Calvanto Group</div></div>
    <div class="services">Buy<span>|</span>Sell<span>|</span>Rent</div>

    <div class="name-marker"></div>
    <h1 class="person-name">Daniel Tran</h1>
    <p class="person-title">Director</p>
    <div class="divider"></div>

    <ul class="contact">
      <li><svg viewBox="0 0 24 24"><path d="M6.6 10.8a15.1 15.1 0 0 0 6.6 6.6l2.2-2.2c.3-.3.7-.4 1-.2 1.1.4 2.3.6 3.6.6.6 0 1 .4 1 1V20c0 .6-.4 1-1 1A17 17 0 0 1 3 4c0-.6.4-1 1-1h3.5c.6 0 1 .4 1 1 0 1.3.2 2.5.6 3.6.1.3 0 .7-.2 1z"/></svg>0400 555 318</li>
      <li><svg viewBox="0 0 24 24"><path d="M2 5h20v14H2z"/><path d="M3 6l9 7 9-7" stroke="#fff" stroke-width="1.6" fill="none"/></svg>daniel.tran@calvanto.com.au</li>
    </ul>

    <div class="company"><strong>Calvanto Group</strong><br>ABN: 12 345 678 901</div>

    <div class="band-purple"></div>
    <div class="band-orange"><a href="http://www.calvanto.com.au/">www.calvanto.com.au</a></div>
  </section>

  <section class="card card-back" aria-label="Business card back">
    <div class="headshot" role="img" aria-label="Head-and-shoulders photo of the director in a navy suit and blue tie"></div>
    <div class="back-brand">Calvanto</div>
    <a class="back-url" href="http://www.calvanto.com.au/">www.calvanto.com.au</a>
  </section>
</body>
</html>
```